Professional looking Roller Blind Discount Card that portrays quality at a value for money price!

We need a double sided business card designed as a discount card. Size 90mm wide x 55mm high.We would like it to look professional and portray quality at a value for money price point.I have uploaded a word document with a basic layout with the information we want included on each side of the card. Please put your own thought into the layout.

Contact Information for Business Card

As per word document attached.

```html
<!DOCTYPE html>
<html lang="en">
<head>
<meta charset="utf-8">
<title>Roller Blinds Discount Card</title>
<link rel="stylesheet" href="https://fonts.googleapis.com/css2?family=Poppins:wght@400;500;700&family=Fjalla+One&family=Oswald:wght@300&family=Great+Vibes&display=swap">
<style>
  :root {
    --blue: #29a8e0;
    --blue-deep: #1a7fd6;
    --blue-light: #6fcdf3;
    --ink: #444448;
    --white: #ffffff;
    --stage: #9b9b9b;
  }
  * { box-sizing: border-box; margin: 0; padding: 0; }
  html, body { width: 1133px; height: 1200px; overflow: hidden; }
  body { background: var(--stage); font-family: "Poppins", sans-serif; position: relative; }

  .card { position: absolute; background: var(--white); overflow: hidden; }

  /* Front side */
  .card--offer { left: 219px; top: 153px; width: 695px; height: 396px; }
  .offer-headline {
    position: absolute; left: 0; right: 0; top: 16px;
    display: flex; justify-content: center; align-items: center; gap: 6px;
    color: var(--blue); font-weight: 700; font-size: 96px; line-height: 1; letter-spacing: -1px;
  }
  .offer-rule { width: 84px; height: 12px; border-top: 2px solid var(--blue); border-bottom: 2px solid var(--blue); position: relative; }
  .offer-rule::after { content: ""; position: absolute; left: 0; right: 0; top: 3px; border-top: 2px solid var(--blue); }
  .offer-sub {
    position: absolute; left: 0; right: 0; top: 95px; text-align: center;
    color: var(--ink); font-size: 31px; line-height: 33px;
  }
  .badges { position: absolute; left: 0; right: 0; top: 176px; height: 156px; }
  .badge {
    position: absolute; top: 0; width: 156px; height: 156px; border-radius: 50%;
    background: linear-gradient(180deg, var(--blue-light) 0%, var(--blue) 50%, var(--blue-deep) 100%);
    border: 4px solid var(--blue);
    box-shadow: inset 0 0 0 3px var(--white);
    display: flex; flex-direction: column; align-items: center; justify-content: center;
    color: var(--white); text-align: center;
  }
  .badge:nth-child(1) { left: 90px; }
  .badge:nth-child(2) { left: 272px; }
  .badge:nth-child(3) { left: 450px; }
  .badge-title { font-family: "Fjalla One", sans-serif; font-size: 22px; line-height: 1.1; }
  .badge-line { font-family: "Oswald", sans-serif; font-weight: 300; font-size: 16px; line-height: 1.3; }
  .offer-call {
    position: absolute; left: 0; right: 0; top: 346px; text-align: center;
    color: var(--ink); font-size: 30px; line-height: 1;
  }
  .phone { color: var(--blue); font-weight: 700; }
  .offer-band { position: absolute; left: 0; right: 0; bottom: 0; height: 8px; background: var(--blue); }

  /* Back side */
  .card--intro { left: 216px; top: 647px; width: 698px; height: 399px; }
  .intro-title {
    position: absolute; left: 26px; top: 16px;
    color: var(--blue); font-weight: 700; font-size: 90px; line-height: 1; letter-spacing: -1px;
  }
  .intro-sub { position: absolute; left: 27px; top: 92px; color: var(--ink); font-size: 40px; line-height: 1.2; }
  .intro-photo {
    position: absolute; left: 28px; top: 142px; width: 429px; height: 181px;
    background: linear-gradient(90deg, #6e5a55 0%, #7d6a63 28%, #6f8a52 45%, #95a884 65%, #5d7a45 85%, #b9b7b0 100%);
  }
  .intro-call {
    position: absolute; left: 28px; top: 323px; width: 429px; height: 50px;
    background: var(--blue); color: var(--white);
    font-size: 32px; line-height: 50px; text-align: center;
  }
  .intro-call strong { font-weight: 700; }
  .fabric-bubble { position: absolute; left: 485px; top: 150px; width: 176px; height: 120px; }
  .fabric-text { font-family: "Great Vibes", cursive; font-size: 25px; fill: var(--white); }
  .company-name {
    position: absolute; left: 480px; right: 12px; top: 348px; text-align: center;
    color: var(--blue); font-size: 24px; font-weight: 500; line-height: 1;
  }
</style>
</head>
<body>

<section class="card card--offer">
  <div class="offer-headline"><span class="offer-rule"></span><span>25% OFF</span><span class="offer-rule"></span></div>
  <p class="offer-sub">Quality Custom Made Roller Blinds<br>Blockout - screen - LightFiltering</p>

  <div class="badges">
    <div class="badge"><span class="badge-title">FREE in Home</span><span class="badge-line">MEASURE &amp; QUOTE</span></div>
    <div class="badge"><span class="badge-title">Best Price</span><span class="badge-line">GUARANTEE</span></div>
    <div class="badge"><span class="badge-title">Family</span><span class="badge-line">OWNED &amp; OPERATED</span></div>
  </div>

  <p class="offer-call">CALL <span class="phone">0400 123 456</span> TODAY!</p>
  <div class="offer-band"></div>
</section>

<section class="card card--intro">
  <h1 class="intro-title">ROLLER BLINDS</h1>
  <p class="intro-sub">FREE in Home Measure &amp; Quote</p>
  <div class="intro-photo" role="img" aria-label="Interior window with roller blind opening onto a leafy garden"></div>
  <p class="intro-call">CALL <strong>0400 123 456</strong> TODAY!</p>

  <svg class="fabric-bubble" viewBox="0 0 176 120">
    <defs>
      <linearGradient id="bubbleFill" x1="0" y1="0" x2="1" y2="1">
        <stop offset="0" stop-color="#8fdaf7"/>
        <stop offset="0.55" stop-color="#2da8ea"/>
        <stop offset="1" stop-color="#1470e0"/>
      </linearGradient>
    </defs>
    <path d="M88 4 C136 4 172 24 172 52 C172 80 136 100 88 100 C70 100 56 98 44 94 L28 114 L30 88 C12 80 4 66 4 52 C4 24 40 4 88 4 Z" fill="url(#bubbleFill)" stroke="#1a7fd6" stroke-width="1.5"/>
    <text class="fabric-text" x="88" y="46" text-anchor="middle">Huge Selection</text>
    <text class="fabric-text" x="88" y="72" text-anchor="middle">of Fabrics</text>
  </svg>

  <p class="company-name">K&amp;M INTERIORS</p>
</section>

</body>
</html>
```